Revamp Marketing Website For Video Production Website

need to revamp current website www.kestrelfilmstudio.net
reference sites www.vantora.net & http://layoutcrate.net/kestrel/
Use all current content on current kestrel website. I want a revamped modenr look. Sometbing that wows customers.
reference site www.vantora.net
Target Market(s)
business owners
Industry/Entity Type
Video Production
Number of Pages Required
5+ page
Colors
Designer to choose colors to be used in the design.
Requirements
Must have
- need to revamp current website www.kestrelfilmstudio.net
- reference sites www.vantora.net & http://layoutcrate.net/kestrel/
- Use all current content on current kestrel website. I want a revamped modenr look. Sometbing that wows customers.
- reference site www.vantora.net
Nice to have
Should not have

```html
<!DOCTYPE html>
<html lang="en">
<head>
<meta charset="utf-8">
<title>Kestrel – Marketing Videos Made For You</title>
<link href="https://fonts.googleapis.com/css2?family=Montserrat:wght@600;700;800&family=Lato:wght@300;400;700&display=swap" rel="stylesheet">
<style>
:root{
  --navy:#0e1626;
  --navy-deep:#0a101c;
  --blue:#0a8fcf;
  --sky:#35b9ec;
  --ink:#111827;
  --text:#3a3a3a;
  --muted:#8a8f98;
  --light:#f8f8f8;
  --white:#ffffff;
}
*{margin:0;padding:0;box-sizing:border-box}
html,body{width:1200px;height:3000px;overflow:hidden}
body{position:relative;background:var(--white);font-family:'Lato',sans-serif;color:var(--text)}
.abs{position:absolute}

/* header */
.site-header{left:0;top:0;width:1200px;height:104px;background:var(--navy)}
.brand{left:77px;top:24px;color:var(--white)}
.brand-name{font-family:'Montserrat',sans-serif;font-weight:800;font-size:34px;letter-spacing:6px;line-height:38px;display:flex;align-items:center;gap:10px}
.brand-dot{width:14px;height:14px;background:var(--sky)}
.brand-tag{font-family:'Montserrat',sans-serif;font-weight:700;font-size:13px;letter-spacing:1.3px;margin-top:6px}
.main-nav{left:398px;top:40px;display:flex;gap:0;font-size:17px;color:#cfd5df}
.main-nav a{color:inherit;text-decoration:none;position:relative;margin-right:31px}
.main-nav a.active{color:var(--sky)}
.main-nav a.active::after{content:"";position:absolute;left:50%;top:30px;margin-left:-6px;border:6px solid transparent;border-bottom-color:var(--sky);border-top:0}
.sign-in{left:1019px;top:26px;width:103px;height:52px;border-radius:26px;background:var(--sky);color:var(--white);font-family:'Montserrat',sans-serif;font-weight:700;font-size:16px;display:flex;align-items:center;justify-content:center}

/* hero */
.hero{left:0;top:104px;width:1200px;height:625px;background:linear-gradient(180deg,#5f6a72 0%,#4d5a55 40%,#3f4a3c 62%,#2d3a52 85%,#3a4048 100%)}
.hero-shade{left:0;top:104px;width:1200px;height:625px;background:rgba(10,16,28,.35)}
.hero-title{left:0;top:222px;width:1200px;text-align:center;color:var(--white);font-family:'Montserrat',sans-serif;font-weight:700;font-size:58px;line-height:68px;letter-spacing:-1px}
.hero-sub{left:0;top:370px;width:1200px;text-align:center;color:var(--white);font-size:31px}
.hero-cta{left:423px;top:438px;width:354px;height:51px;border-radius:26px;background:var(--sky);color:var(--white);font-family:'Montserrat',sans-serif;font-weight:700;font-size:16px;display:flex;align-items:center;justify-content:center;letter-spacing:-.2px}

/* features */
.features{left:77px;top:626px;width:1045px;height:333px;background:var(--blue)}
.features-title{left:130px;top:684px;color:var(--white);font-family:'Montserrat',sans-serif;font-weight:700;font-size:42px;line-height:52px}
.features-copy{left:433px;top:683px;width:640px;color:var(--white);font-size:14px;line-height:26px}
.feature-card{top:864px;width:193px;height:193px;background:var(--white);box-shadow:0 2px 8px rgba(0,0,0,.12);text-align:center;font-size:21px;line-height:29px;color:var(--ink)}
.feature-card svg{display:block;margin:26px auto 12px}
.arrow{top:935px;width:46px;height:46px;border-radius:50%;border:3px solid var(--white);display:flex;align-items:center;justify-content:center;box-shadow:0 1px 4px rgba(0,0,0,.25)}
.arrow.prev{left:103px;background:#222}
.arrow.next{left:1051px;background:#8a8d92}

/* examples */
.section-title{left:0;width:1200px;text-align:center;font-family:'Montserrat',sans-serif;font-weight:700;font-size:42px;color:var(--ink);letter-spacing:-1px}
.example{width:333px;height:220px}
.btn-dark{left:496px;top:1730px;width:208px;height:62px;background:var(--navy);color:var(--white);font-family:'Montserrat',sans-serif;font-weight:700;font-size:16px;display:flex;align-items:center;justify-content:center;letter-spacing:-.3px}

/* sizes */
.sizes-bg{left:0;top:1835px;width:1200px;height:770px}
.size-img{top:2068px;width:333px;height:317px;box-shadow:0 1px 4px rgba(0,0,0,.12)}
.size-title{top:2403px;font-size:26px;color:var(--sky)}
.size-copy{top:2442px;width:333px;font-size:15px;line-height:26px;color:var(--muted);font-weight:300}

/* footer */
.site-footer{left:0;top:2605px;width:1200px;height:302px;background:var(--navy)}
.footer-brand{left:0;top:2664px;width:1200px;text-align:center;color:var(--white)}
.footer-brand .brand-name{justify-content:center}
.footer-nav{left:0;top:2749px;width:1200px;text-align:center;color:var(--white);font-size:15px}
.footer-nav span{margin:0 10px}
.social{top:2801px;width:52px;height:52px;border-radius:50%;border:1.5px solid #cfd5df}
.copyright-bar{left:0;top:2907px;width:1200px;height:93px;background:var(--navy-deep);border-top:1px solid #1d2638}
.copyright{left:0;top:2947px;width:1200px;text-align:center;font-size:13px;color:#9aa1ad}
.copyright b{color:var(--white);font-weight:700}
</style>
</head>
<body>

<header class="site-header abs"></header>
<div class="brand abs">
  <div class="brand-name"><span class="brand-dot"></span>KESTREL</div>
  <div class="brand-tag">MARKETING VIDEOS MADE FOR YOU</div>
</div>
<nav class="main-nav abs">
  <a class="active">Home</a><a>How It Works</a><a>Examples</a><a>Faq</a><a>Contact Us</a><a>Pricing</a>
</nav>
<div class="sign-in abs">SIGN IN</div>

<div class="hero abs" role="img" aria-label="Two people looking out over a park toward a city skyline"></div>
<div class="hero-shade abs"></div>
<h1 class="hero-title abs">ATTENTION GRABBING<br>VIDEO ADS</h1>
<p class="hero-sub abs">Delivered in 24 Hours!</p>
<div class="hero-cta abs">GET ONE FREE VIDEO MOCKUP NOW</div>

<section class="features abs"></section>
<h2 class="features-title abs">OUR<br>FEATURES</h2>
<p class="features-copy abs">Lorem ipsum dolor sit amet, consectetur adipiscing elit, sed do eiusmod tempor incididunt labore et dolore magna aliqua. Ut enim ad minim veniam, quis nostrud exercitation ullamco laboris nisi ut aliquip ex ea commodo consequat. Duis aute irure dolor in reprehenderit in voluptate velit esse cillum dolore eu fugiat nulla pariatur.</p>

<div class="feature-card abs" style="left:168px">
  <svg width="76" height="72" viewBox="0 0 76 72" fill="none" stroke="#35b9ec" stroke-width="2.5"><rect x="2" y="10" width="58" height="58"/><path d="M16 36l14 16 42-50"/></svg>
  Done For You
</div>
<div class="feature-card abs" style="left:391px">
  <svg width="60" height="72" viewBox="0 0 60 72" fill="none" stroke="#35b9ec" stroke-width="2"><circle cx="30" cy="28" r="24"/><circle cx="30" cy="28" r="17"/><path d="M21 28l7 7 12-13"/><path d="M16 48l-4 22 18-10 18 10-4-22"/></svg>
  Premium<br>Content
</div>
<div class="feature-card abs" style="left:615px">
  <svg width="60" height="72" viewBox="0 0 60 72" fill="none" stroke="#35b9ec" stroke-width="2"><rect x="4" y="2" width="52" height="68"/><path d="M14 12h32M14 20h32"/><path d="M30 30l4 8 9 1-6 6 2 9-9-5-9 5 2-9-6-6 9-1z"/><path d="M22 54l-4 10M38 54l4 10"/></svg>
  Fully Licensed<br>to you
</div>
<div class="feature-card abs" style="left:839px">
  <svg width="72" height="72" viewBox="0 0 72 72" fill="none" stroke="#35b9ec" stroke-width="2"><circle cx="36" cy="24" r="14"/><path d="M20 26v-6a16 16 0 0132 0v6"/><rect x="16" y="22" width="6" height="10"/><rect x="50" y="22" width="6" height="10"/><path d="M53 32c0 8-8 10-14 10"/><path d="M6 70V58c0-8 10-12 18-14l12 12 12-12c8 2 18 6 18 14v12"/></svg>
  Best Support
</div>
<div class="arrow prev abs"><svg width="22" height="18" viewBox="0 0 22 18" fill="none" stroke="#fff" stroke-width="2.5"><path d="M21 9H3M10 2L3 9l7 7"/></svg></div>
<div class="arrow next abs"><svg width="22" height="18" viewBox="0 0 22 18" fill="none" stroke="#fff" stroke-width="2.5"><path d="M1 9h18M12 2l7 7-7 7"/></svg></div>

<h2 class="section-title abs" style="top:1120px">OUR EXAMPLES</h2>
<div class="example abs" role="img" aria-label="Costumed mascots parading in a station" style="left:77px;top:1208px;background:linear-gradient(135deg,#2d6fb0,#d8b12a 55,#3a3a46)"></div>
<div class="example abs" role="img" aria-label="Man in sunglasses beside a child under blue sky" style="left:433px;top:1208px;background:linear-gradient(135deg,#1f7fd6,#e9a3a8 55%,#2c2b2a)"></div>
<div class="example abs" role="img" aria-label="Two women with shopping bags on a street" style="left:790px;top:1208px;background:linear-gradient(135deg,#c9cfd4,#b88a6c 50%,#5c6770)"></div>
<div class="example abs" role="img" aria-label="Two friends jumping on a beach" style="left:77px;top:1454px;background:linear-gradient(180deg,#1ab0b8,#0f8fa0 70%,#e8e1d2)"></div>
<div class="example abs" role="img" aria-label="Hand holding a phone in an old town street" style="left:433px;top:1454px;background:linear-gradient(135deg,#6e4b3a,#d9b89c 50%,#5a4033)"></div>
<div class="example abs" role="img" aria-label="Salad bowl and flatbread on a table" style="left:790px;top:1454px;background:linear-gradient(135deg,#3a2c26,#8aa34a 50%,#b33226)"></div>
<div class="btn-dark abs">SEE ALL EXAMPLES</div>

<svg class="sizes-bg abs" width="1200" height="770" viewBox="0 0 1200 770"><path d="M0 62L1200 0V770H0z" fill="#f8f8f8"/></svg>
<h2 class="section-title abs" style="top:1933px">VIDEO SIZES AVAILABLE</h2>

<div class="size-img abs" role="img" aria-label="Woman hugging a spotted dog against a pink wall" style="left:77px;background:linear-gradient(180deg,#f3c2bf,#f4e4dc 80%,#f8ecea)"></div>
<div class="size-img abs" role="img" aria-label="Woman lying on a boat deck over turquoise water" style="left:433px;background:linear-gradient(90deg,#f0efe9 45%,#1fb0c0 60%,#10a0b4)"></div>
<div class="size-img abs" role="img" aria-label="Hand holding an ice cream cone" style="left:790px;background:linear-gradient(135deg,#cfd8de,#e8a6b8 50%,#b8c2c8)"></div>

<h3 class="size-title abs" style="left:79px">Wide Screen Videos</h3>
<p class="size-copy abs" style="left:79px">This size is a standard video size that works best for pretty much anywhere on the web (1080x720) Included with all video purchases</p>
<h3 class="size-title abs" style="left:435px">Square Videos</h3>
<p class="size-copy abs" style="left:435px">Square Videos that work best on CIRCLEFEED (Square is 1080 X 1080) Convert any video to this size for an additional fee of $39</p>
<h3 class="size-title abs" style="left:792px">Vertical Videos</h3>
<p class="size-copy abs" style="left:792px">Vertical Videos that work best on STORIES for Circlefeed, Snapgrid and Flashtalk (1080 X 1920) Convert any video to this size for an additional fee of $39</p>

<footer class="site-footer abs"></footer>
<div class="footer-brand abs">
  <div class="brand-name"><span class="brand-dot"></span>KESTREL</div>
  <div class="brand-tag">MARKETING VIDEOS MADE FOR YOU</div>
</div>
<nav class="footer-nav abs">Home<span>|</span>How It Works<span>|</span>Examples<span>|</span>Faqs<span>|</span>Contact Us<span>|</span>Pricing</nav>
<div class="social abs" style="left:448px" aria-label="Social link 1"></div>
<div class="social abs" style="left:511px" aria-label="Social link 2"></div>
<div class="social abs" style="left:574px" aria-label="Social link 3"></div>
<div class="social abs" style="left:637px" aria-label="Social link 4"></div>
<div class="social abs" style="left:699px" aria-label="Social link 5"></div>

<div class="copyright-bar abs"></div>
<p class="copyright abs">© <b>KESTREL VIDEO MARKETING FOR YOU</b> - 2019 . All Right Reserved</p>

</body>
</html>
```